Stonebridge Building and Projects business cards

A business card with watermark background (construction work)

Company logo attached

Home improvement projects
House renovations
Bathroom and kitchen renovations
House extensions
New builds and granny flats

Director Omar Haddani
(Phone number)
omar@sbpbuilding.com.au
(Instagram logo) sbp_building

```html
<!DOCTYPE html>
<html lang="en">
<head>
<meta charset="utf-8">
<title>Stonebridge Building and Projects – Business Cards</title>
<link href="https://fonts.googleapis.com/css2?family=Poppins:wght@300;400;600;700&display=swap" rel="stylesheet">
<style>
  :root {
    --brand-blue: #2c6ca6;
    --brand-blue-dark: #245d91;
    --paper: #f6f7f8;
    --stage: #e9eaec;
    --band-grey: #c9cbcf;
    --ink: #3a3d42;
    --ink-soft: #5c6067;
    --white: #ffffff;
  }
  * { margin: 0; padding: 0; box-sizing: border-box; }
  html, body {
    width: 1200px; height: 944px; overflow: hidden;
    background: var(--stage);
    font-family: "Poppins", sans-serif;
  }
  .sheet {
    width: 1200px; height: 944px;
    display: flex; align-items: center; justify-content: center; gap: 40px;
  }
  .card {
    position: relative;
    width: 560px; height: 320px;
    overflow: hidden;
    box-shadow: 0 10px 28px rgba(0,0,0,.12);
  }

  /* Front face */
  .card--front {
    background: var(--brand-blue);
    color: var(--white);
    display: flex; flex-direction: column; align-items: center;
  }
  .wordmark {
    display: flex; align-items: center; gap: 10px;
    font-weight: 600; letter-spacing: .2px;
  }
  .wordmark__square { width: 14px; height: 14px; flex: none; }
  .card--front .wordmark { margin-top: 92px; font-size: 22px; }
  .card--front .wordmark__square { background: var(--white); }
  .services {
    margin-top: 56px;
    text-align: center;
    font-weight: 300; font-size: 13.5px; line-height: 1.6;
  }

  /* Back face */
  .card--back { background: var(--paper); }
  .watermark-photo {
    position: absolute; inset: 0 0 90px 0;
    background: radial-gradient(ellipse at 62% 40%, #e4e6e8 0%, #eef0f1 45%, var(--paper) 80%);
    opacity: .9;
  }
  .wave { position: absolute; left: 0; bottom: 0; width: 560px; height: 200px; }
  .back-content {
    position: absolute; left: 0; top: 78px; width: 100%;
    display: flex; align-items: center;
  }
  .card--back .wordmark {
    width: 230px; justify-content: flex-end; padding-right: 18px;
    font-size: 15px; color: var(--brand-blue);
  }
  .card--back .wordmark__square { background: var(--brand-blue); width: 11px; height: 11px; }
  .divider { width: 1px; height: 112px; background: var(--brand-blue); opacity: .7; }
  .contact { padding-left: 20px; }
  .contact__name { font-weight: 700; font-size: 21px; color: var(--brand-blue); line-height: 1.1; }
  .contact__role { font-weight: 400; font-size: 11.5px; color: var(--ink-soft); margin-bottom: 10px; }
  .contact__list { list-style: none; font-size: 11.5px; color: var(--ink); }
  .contact__list li { display: flex; align-items: center; gap: 8px; line-height: 1.75; }
  .icon { width: 12px; height: 12px; flex: none; }
  .icon--dot { width: 9px; height: 9px; margin: 0 1.5px; border-radius: 50%; background: var(--brand-blue); }
</style>
</head>
<body>
<main class="sheet">
  <section class="card card--front" aria-label="Business card front">
    <div class="wordmark">
      <span class="wordmark__square"></span>
      <span class="wordmark__name">Stonebridge Building and Projects</span>
    </div>
    <p class="services">
      Home improvement projects • House renovations<br>
      Bathroom and kitchen renovations • House extensions<br>
      New builds and granny flats
    </p>
  </section>

  <section class="card card--back" aria-label="Business card back">
    <div class="watermark-photo" role="img" aria-label="Faint watermark photo of hands holding keys over a small house model and building plans"></div>
    <svg class="wave" viewBox="0 0 560 200" preserveAspectRatio="none" aria-hidden="true">
      <path d="M0 120 C150 120 260 90 360 60 C450 32 520 12 560 0 L560 200 L0 200 Z" fill="var(--band-grey)"/>
      <path d="M0 134 C160 134 270 106 370 76 C460 48 525 26 560 16 L560 200 L0 200 Z" fill="var(--brand-blue)"/>
    </svg>
    <div class="back-content">
      <div class="wordmark">
        <span class="wordmark__square"></span>
        <span class="wordmark__name">Stonebridge Building<br>and Projects</span>
      </div>
      <div class="divider"></div>
      <div class="contact">
        <h1 class="contact__name">Omar Haddani</h1>
        <p class="contact__role">Managing Director</p>
        <ul class="contact__list">
          <li>
            <svg class="icon" viewBox="0 0 12 12" aria-hidden="true"><path d="M2.5 1 L4.5 1 L5.3 3.4 L4 4.4 C4.6 5.8 6.2 7.4 7.6 8 L8.6 6.7 L11 7.5 L11 9.5 C11 10.3 10.3 11 9.5 11 C5 11 1 7 1 2.5 C1 1.7 1.7 1 2.5 1 Z" fill="var(--brand-blue)"/></svg>
            (012) 555-0147
          </li>
          <li>
            <svg class="icon" viewBox="0 0 12 12" aria-hidden="true"><rect x="0.5" y="2.5" width="11" height="7.5" rx="1" fill="var(--brand-blue)"/><path d="M1 3 L6 6.8 L11 3" stroke="var(--paper)" stroke-width="1" fill="none"/></svg>
            omar@sbpbuilding.com.au
          </li>
          <li>
            <span class="icon icon--dot" aria-hidden="true"></span>
            @sbp_building
          </li>
        </ul>
      </div>
    </div>
  </section>
</main>
</body>
</html>
```